Software Product Flyer Design

A established czech software company needs a marketing flyer to promote their software product and its modules.
The overall feel of the flyer must to be serious, but also eye-catching, enticing, clever and bold to attract customers.
Unifying graphic element is the new product logo.
The flyer would be A4, colour both sides and folded once (to give 4 pages of A5).
Title page - product logo with module name and module icon, short presentation of the product and list of its key features.
Inside pages - detailed informations with screenshots or graphical schemas.
Back side - informations about technical requirements and user support, contacts (address, phone, fax, e-mail, web pages - no social networks).
Product logo, module icon and some images attached.
Updates
Hello,
Reason: For organizational reasons we extending the deadline by 10 days.
FYI: We have uploaded the new ZIP file with previous version of our flyer.
Attached PDF file with text for inner pages.
Target Market(s)
Existing or new customers like municipalities, public authorities and nonprofit organizations.
Industry/Entity Type
Marketing
Requirements
Must have
- Winning designer must provide a template for Adobe InDesign based on his graphic design.
Avoid to using exotic fonts - in Czech we use Latin Extended characters (like áéěíýůčřžšťďň).
Nice to have
- Using graphic motif from product logo like as attached splash screen.

```html
<!DOCTYPE html>
<html lang="en">
<head>
<meta charset="utf-8">
<title>Veltra Product Flyer</title>
<link rel="stylesheet" href="https://fonts.googleapis.com/css2?family=Open+Sans:ital,wght@0,300;0,400;0,600;0,700;1,400&display=swap">
<style>
  :root {
    --slate: #4b5058;
    --paper: #ffffff;
    --paper-shade: #d9dbde;
    --footer: #e4e5e7;
    --ink: #2b2d31;
    --ink-soft: #55585e;
    --on-slate: #eef0f2;
    --on-slate-soft: #d8dbe0;
    --stage: #ebe8e3;
  }
  * { box-sizing: border-box; margin: 0; padding: 0; }
  html, body { width: 1200px; height: 900px; overflow: hidden; }
  body {
    background: var(--stage);
    font-family: "Open Sans", Arial, sans-serif;
    position: relative;
  }
  .flyer {
    position: absolute;
    top: 70px;
    width: 540px;
    height: 760px;
    background: var(--slate);
    overflow: hidden;
    box-shadow: 0 6px 18px rgba(0,0,0,.18);
  }
  .flyer--a { left: 40px; }
  .flyer--b { left: 620px; }

  .screenshot {
    position: absolute;
    background: linear-gradient(180deg, #eef1f3 0%, #d9dee2 100%);
    border: 3px solid #c9d3d6;
  }
  .light-band {
    position: absolute;
    background: linear-gradient(90deg, #c9ccd0 0%, #ffffff 100%);
  }
  .title {
    font-weight: 300;
    color: var(--on-slate);
    font-size: 17.5px;
    line-height: 1.3;
  }
  .body-text {
    font-size: 10.5px;
    line-height: 1.42;
    text-align: justify;
  }
  .on-slate .body-text { color: var(--on-slate-soft); }
  .text-block { position: absolute; }

  .white-box {
    position: absolute;
    background: linear-gradient(90deg, var(--paper) 0%, var(--paper) 70%, var(--paper-shade) 100%);
    padding: 26px 30px 22px 30px;
  }
  .white-box .area-title {
    font-weight: 700;
    font-size: 12px;
    color: var(--ink);
    margin-bottom: 2px;
  }
  .white-box .body-text { color: var(--ink); }
  .white-box .area { margin-bottom: 22px; }
  .footnote {
    border-top: 1.5px solid var(--ink);
    padding-top: 4px;
    font-size: 7px;
    line-height: 1.35;
    color: var(--ink-soft);
    width: 86%;
  }

  .brand {
    position: absolute;
    left: 0; right: 0;
    text-align: center;
  }
  .brand-name {
    font-weight: 600;
    font-size: 46px;
    color: var(--on-slate);
    letter-spacing: .5px;
  }

  .contact-bar {
    position: absolute;
    left: 0; right: 0; bottom: 0;
    height: 60px;
    background: var(--footer);
    display: flex;
    align-items: center;
    justify-content: space-between;
    padding: 0 40px;
    color: var(--ink);
    font-size: 10.5px;
    line-height: 1.25;
  }
  .contact-item { display: flex; align-items: center; gap: 6px; }
  .contact-item svg { flex: none; }
</style>
</head>
<body>

<!-- Layout A -->
<section class="flyer flyer--a on-slate">
  <div class="light-band" style="left:0; top:200px; width:540px; height:50px;"></div>
  <div class="screenshot" role="img" aria-label="Software screenshot showing the product's data table window" style="left:26px; top:26px; width:230px; height:200px;"></div>

  <div class="text-block" style="left:278px; top:24px; width:240px;">
    <h2 class="title">Title of the Text</h2>
    <p class="body-text" style="margin-top:6px;">Sed ut perspiciatis unde omnis iste natus error sit voluptatem accusantium doloremque laudantium, totam rem aperiam, eaque ipsa quae ab illo inventore veritatis et quasi architecto beatae vitae dicta sunt explicabo. Sed ut perspiciatis unde omnis iste natus error sit voluptatem accusantium doloremque</p>
  </div>

  <div class="white-box" style="left:222px; top:236px; width:318px;">
    <div class="area">
      <h3 class="area-title">Some Text Area</h3>
      <p class="body-text">Sed ut perspiciatis unde omnis iste natus error sit voluptatem accusantium doloremque laudantium, totam rem aperiam, eaque ipsa quae ab illo inventore veritatis et quasi architecto beatae vitae dicta sunt explicabo.</p>
    </div>
    <div class="area">
      <h3 class="area-title">Some Text Area</h3>
      <p class="body-text">Sed ut perspiciatis unde omnis iste natus error sit voluptatem accusantium doloremque laudantium, totam rem aperiam, eaque ipsa quae ab illo inventore veritatis et quasi architecto beatae vitae dicta sunt explicabo.</p>
    </div>
    <p class="footnote">Sed ut perspiciatis unde omnis iste natus error sit voluptatem accusantium doloremque laudantium, totam rem aperiam</p>
  </div>

  <div class="text-block" style="left:22px; top:270px; width:186px;">
    <h2 class="title">Here May be Another Secondary Title</h2>
    <p class="body-text" style="margin-top:8px;">Sed ut perspiciatis unde omnis iste natus error sit voluptatem accusantium doloremque laudantium, totam rem aperiam, eaque ipsa quae ab illo inventore veritatis et quasi architecto beatae vitae dicta sunt explicabo. Sed ut perspiciatis unde omnis iste natus error sit voluptatem accusantium doloremque laudantium, totam rem aperiam, eaque ipsa quae ab illo inventore veritatis et quasi architecto beatae vitae dicta sunt explicabo.</p>
  </div>

  <div class="brand" style="top:600px;">
    <span class="brand-name">Veltra</span>
  </div>

  <footer class="contact-bar">
    <div class="contact-item">
      <svg width="22" height="22" viewBox="0 0 22 22" fill="none" stroke="#2b2d31" stroke-width="1.6"><path d="M2 10 L11 3 L20 10"/><rect x="5" y="10" width="12" height="10"/></svg>
      <span>VELTRA LTD<br>24 Brook Lane, Country</span>
    </div>
    <div class="contact-item">
      <svg width="16" height="16" viewBox="0 0 16 16" fill="none" stroke="#2b2d31" stroke-width="1.5"><circle cx="8" cy="8" r="6.5"/><circle cx="8" cy="8" r="2.5"/></svg>
      <span>info@veltra.example</span>
    </div>
    <div class="contact-item">
      <svg width="16" height="20" viewBox="0 0 16 20" fill="none" stroke="#2b2d31" stroke-width="1.5"><rect x="2" y="1" width="12" height="18" rx="1.5"/><line x1="5" y1="6" x2="11" y2="6"/><line x1="5" y1="10" x2="11" y2="10"/><line x1="5" y1="14" x2="11" y2="14"/></svg>
      <span>+1 555 010 2030</span>
    </div>
  </footer>
</section>

<!-- Layout B -->
<section class="flyer flyer--b on-slate">
  <div class="light-band" style="left:0; top:190px; width:540px; height:40px;"></div>
  <div class="screenshot" role="img" aria-label="Software screenshot showing the product's data table window" style="left:292px; top:24px; width:226px; height:200px;"></div>

  <div class="text-block" style="left:26px; top:24px; width:250px;">
    <h2 class="title">Title of the Text</h2>
    <p class="body-text" style="margin-top:6px;">Sed ut perspiciatis unde omnis iste natus error sit voluptatem accusantium doloremque laudantium, totam rem aperiam, eaque ipsa quae ab illo inventore veritatis et quasi architecto beatae vitae dicta sunt explicabo. Sed ut perspiciatis unde omnis iste natus error sit voluptatem accusantium doloremque</p>
  </div>

  <div class="white-box" style="left:0; top:224px; width:312px;">
    <div class="area">
      <h3 class="area-title">Some Text Area</h3>
      <p class="body-text">Sed ut perspiciatis unde omnis iste natus error sit voluptatem accusantium doloremque laudantium, totam rem aperiam, eaque ipsa quae ab illo inventore veritatis et quasi architecto beatae vitae dicta sunt explicabo.</p>
    </div>
    <div class="area">
      <h3 class="area-title">Some Text Area</h3>
      <p class="body-text">Sed ut perspiciatis unde omnis iste natus error sit voluptatem accusantium doloremque laudantium, totam rem aperiam, eaque ipsa quae ab illo inventore veritatis et quasi architecto beatae vitae dicta sunt explicabo.</p>
    </div>
    <p class="footnote">Sed ut perspiciatis unde omnis iste natus error sit voluptatem accusantium doloremque laudantium, totam rem aperiam</p>
  </div>

  <div class="text-block" style="left:328px; top:250px; width:192px;">
    <h2 class="title">Here May be Another Secondary Title</h2>
    <p class="body-text" style="margin-top:8px;">Sed ut perspiciatis unde omnis iste natus error sit voluptatem accusantium doloremque laudantium, totam rem aperiam, eaque ipsa quae ab illo inventore veritatis et quasi architecto beatae vitae dicta sunt explicabo. Sed ut perspiciatis unde omnis iste natus error sit voluptatem accusantium doloremque laudantium, totam rem aperiam, eaque ipsa quae ab illo inventore veritatis et quasi architecto beatae vitae dicta sunt explicabo.</p>
  </div>

  <div class="brand" style="top:600px;">
    <span class="brand-name">Veltra</span>
  </div>

  <footer class="contact-bar">
    <div class="contact-item">
      <svg width="22" height="22" viewBox="0 0 22 22" fill="none" stroke="#2b2d31" stroke-width="1.6"><path d="M2 10 L11 3 L20 10"/><rect x="5" y="10" width="12" height="10"/></svg>
      <span>VELTRA LTD<br>24 Brook Lane, Country</span>
    </div>
    <div class="contact-item">
      <svg width="16" height="16" viewBox="0 0 16 16" fill="none" stroke="#2b2d31" stroke-width="1.5"><circle cx="8" cy="8" r="6.5"/><circle cx="8" cy="8" r="2.5"/></svg>
      <span>info@veltra.example</span>
    </div>
    <div class="contact-item">
      <svg width="16" height="20" viewBox="0 0 16 20" fill="none" stroke="#2b2d31" stroke-width="1.5"><rect x="2" y="1" width="12" height="18" rx="1.5"/><line x1="5" y1="6" x2="11" y2="6"/><line x1="5" y1="10" x2="11" y2="10"/><line x1="5" y1="14" x2="11" y2="14"/></svg>
      <span>+1 555 010 2030</span>
    </div>
  </footer>
</section>

</body>
</html>
```